Life Timeline of a Man's Career

We want to create a timeline of our director's career to be printed in
with pictures. More looking like a memory lane.

Nom : Gérard Malouin

1. Date de naissance : 28 décembre 1951
2. Vécu jusqu’à ses 23 ans à Rennes
3. Travaillé en Bretagne comme surveillant et documentaliste
4. En 1974 rencontre sa femme (Sylvie) lors d’un voyage en ex-Yougoslavie
5. Mariage : 5 avril 1975
6. 1er enfant : 1978
7. 2ème enfant : 1981
8. Demande de formation professionnelle comme cadre d’école : 1987
9. Sous-Directeur Collège Bretagne : 1988-1991
10. Directeur Lycée Français en Australie : 1991-1997
11. Achat vielle école en Dordogne (France) : 1997
12. Directeur Lycée Français à Ottawa (Canada): 2000
13. Directeur Lycée Varenne Aubrac (France) : 2000-2001
14. Directeur Lycée Français à New-York (USA): 2001-2011
15. Grand-Père de Maëlle : 2007
16. Grand-Père de Basile : 2009
17. Grand-Père de Clémentine : 2011
18. Directeur Collège des Ormeaux à Genève (Suisse) : 2011-2015
19. Grand-Père d’Louise: 2014
20. Grand-Père pour la 5ème fois (Garçon) : 2015
21. Départ à la retraite : 30 juin 2015

Target Market(s)

Gift for a director - to be engraved on a glass

Industry/Entity Type

Education

Requirements
Must have
• same style as the picture attached : the size of the design would be 70 x 100 cm

```html
<!DOCTYPE html>
<html lang="fr">
<head>
<meta charset="utf-8">
<title>Gérard Malouin — Parcours</title>
<link rel="stylesheet" href="https://fonts.googleapis.com/css2?family=Lobster&display=swap">
<style>
  :root {
    --paper: #fcf9dc;
    --label: #f6ebb9;
    --ink: #8a5a2b;
    --bark: #8f6331;
    --leaf-light: #a9cf6a;
    --leaf: #6fa636;
    --leaf-dark: #3f7a1e;
    --title-shadow: #6c9b2c;
    --root: #b08a5a;
  }
  * { margin: 0; padding: 0; box-sizing: border-box; }
  html, body { width: 840px; height: 1200px; overflow: hidden; background: var(--paper); }
  .poster {
    position: relative; width: 840px; height: 1200px; overflow: hidden;
    background: var(--paper); font-family: "Lobster", cursive; color: var(--ink);
  }
  .poster__title {
    position: absolute; top: 26px; left: 0; width: 100%; text-align: center;
    font-size: 86px; font-weight: 400; color: var(--bark); line-height: 1.1;
    text-shadow: 3px 4px 0 var(--title-shadow);
  }
  .tree-crown {
    position: absolute; left: 36px; top: 130px; width: 768px; height: 300px;
    border-radius: 24px;
    background: linear-gradient(180deg, var(--leaf-light) 0%, var(--leaf) 55%, var(--leaf-dark) 100%);
    opacity: 0.55;
  }
  .tree-roots {
    position: absolute; left: 150px; top: 1112px; width: 560px; height: 88px;
    border-radius: 24px 24px 0 0;
    background: linear-gradient(180deg, var(--root) 0%, rgba(176,138,90,0.25) 100%);
    opacity: 0.6;
  }
  .branches { position: absolute; inset: 0; }
  .event {
    position: absolute; height: 44px; background: var(--label);
    display: flex; align-items: center; justify-content: center; text-align: center;
    font-size: 13px; line-height: 1.3; padding: 0 8px; border-radius: 2px;
  }
  .event--wide { width: 225px; }
  .event--narrow { width: 182px; }
  .event--right { width: 222px; }
</style>
</head>
<body>
<main class="poster">
  <div class="tree-crown" role="img" aria-label="Illustration : feuillage vert de l'arbre de vie"></div>
  <div class="tree-roots" role="img" aria-label="Illustration : racines de l'arbre"></div>

  <svg class="branches" width="840" height="1200" viewBox="0 0 840 1200" aria-hidden="true">
    <rect x="405" y="430" width="28" height="682" fill="var(--bark)" />
    <g fill="none" stroke="var(--bark)" stroke-width="3" stroke-linecap="round">
      <path d="M300 475 Q330 500 405 492" />
      <path d="M268 500 Q320 510 405 492" />
      <path d="M300 585 Q330 610 405 605" />
      <path d="M268 612 Q320 620 405 605" />
      <path d="M300 705 Q330 728 405 722" />
      <path d="M268 740 Q320 738 405 722" />
      <path d="M300 815 Q330 845 405 840" />
      <path d="M268 860 Q320 860 405 840" />
      <path d="M300 950 Q340 980 405 970" />
      <path d="M268 980 Q330 975 405 970" />
      <path d="M300 1045 Q330 1010 345 985 Q370 975 405 970" />
      <path d="M530 440 Q500 465 433 470" />
      <path d="M574 475 Q520 470 433 470" />
      <path d="M530 550 Q500 575 433 580" />
      <path d="M574 588 Q520 580 433 580" />
      <path d="M530 676 Q510 700 433 705" />
      <path d="M574 710 Q520 705 433 705" />
      <path d="M530 800 Q505 820 433 828" />
      <path d="M574 833 Q520 830 433 828" />
      <path d="M530 915 Q505 940 433 945" />
      <path d="M574 950 Q520 945 433 945" />
    </g>
  </svg>

  <h1 class="poster__title">Gérard Malouin</h1>

  <div class="event event--wide" style="left:75px;top:430px">Grand-Père de Louise: 2014</div>
  <div class="event event--wide" style="left:43px;top:489px">Directeur Collège des Ormeaux<br>à Genève (Suisse) : 2011-2015</div>
  <div class="event event--narrow" style="left:118px;top:543px">Grand-Père de Maëlle : 2007</div>
  <div class="event event--wide" style="left:43px;top:601px">Directeur Lycée Français à<br>New-York (USA) : 2001-2011</div>
  <div class="event event--narrow" style="left:118px;top:667px">Achat vielle école en<br>Dordogne (France) : 1997</div>
  <div class="event event--wide" style="left:43px;top:727px">Directeur Lycée Français<br>en Australie : 1991-1997</div>
  <div class="event event--wide" style="left:75px;top:789px">2ème enfant : 1981</div>
  <div class="event event--wide" style="left:43px;top:848px">1er enfant : 1978</div>
  <div class="event event--wide" style="left:75px;top:906px">Travaillé en Bretagne comme<br>surveillant et documentaliste</div>
  <div class="event event--wide" style="left:43px;top:965px">Vécu jusqu'à ses 23 ans à Rennes</div>
  <div class="event event--wide" style="left:75px;top:1023px">Date de naissance :<br>28 décembre 1951</div>

  <div class="event event--right" style="left:530px;top:397px">Départ à la retraite :<br>30 juin 2015</div>
  <div class="event event--right" style="left:574px;top:453px">Grand-Père pour la 5ème fois<br>(Garçon) : 2015</div>
  <div class="event event--right" style="left:530px;top:510px">Grand-Père de Clémentine : 2011</div>
  <div class="event event--right" style="left:574px;top:566px">Grand-Père de Basile : 2009</div>
  <div class="event event--right" style="left:530px;top:633px">Directeur Lycée Varenne<br>Aubrac (France) : 2000-2001</div>
  <div class="event event--right" style="left:574px;top:689px">Directeur Lycée Français à<br>Ottawa (Canada): 2000</div>
  <div class="event event--right" style="left:530px;top:756px">Sous-Directeur Collège<br>Bretagne : 1988-1991</div>
  <div class="event event--right" style="left:574px;top:811px">Demande de formation professionnelle<br>comme cadre d'école : 1987</div>
  <div class="event event--right" style="left:530px;top:873px">Mariage : 5 avril 1975</div>
  <div class="event event--right" style="left:574px;top:928px">En 1974 rencontre sa femme (Sylvie)<br>lors d'un voyage en ex-Yougoslavie</div>
</main>
</body>
</html>
```